New design for www.TrimTable.com

On TrimTable you can find & book your hairdresser. TrimTable is the biggest platform in the Netherlands.

- The design should be a responcive design
- Should be able to go global, should fit in perfectly between all the big booking platforms like stayvo, ridlo etc,
- Should have te result of more bookings. :)
- We are ‘only’ asking a beautiful design, not a technical solution.
- We need a homepage (https://trimtable.com/), search resultpage ((https://trimtable.com/kapper/amsterdam/#), salonpage (https://trimtable.com/kapper/vorden/lumo-for-hair/), about us page (https://trimtable.com/aboutus/), for the hairdresser info page (https://trimtable.com/kapper/), login/register page (https://trimtable.com/account/signin/).

- On the page of the hairdresser there is a dynamic part. The part where you create your appointment. Please take a look at this part too after you choose your treatment (behandeling), employee (medewerker), Date (datum) and time (tijd). The part that you see after this, is the part where you fill in your data as a consumer.

I've added more logo's but mostly we use the green color.

A few of our competitors: www.plumsalo.com, www.korifex.com

Target Market(s)

All consumers

Industry/Entity Type

Hair And Beauty

Number of Pages Required

5+ page

Font styles to use
Sans Serif

Colors
abd036
c3c3c3
757575

Requirements
Must have
• Responsive
• We did an A/B test with the homepage. It turns out that option B works better then option A (take a look at the uploaded pictures). So what we need on the homepage: The USP's with the green checkboxes, The search button needs to by dynamic (changes for example from light green to dark green so you can see you can click it) The call to action sentence Zoek & Vind je kapsalon, the searchfield and searchbutton should be seperated.
Nice to have
• The style that we like is the flat design style. The website should be simple, clean and it should feel a bit like a luxury thing. Because an appointment with the hairdresser can be a real treat and luxury moment for yourself.
• The luxury feeling and flat design that is in the www.ridlo.com website is really nice for example. But then it has to be a bit more light and not so black and dark.

```html
<!DOCTYPE html>
<html lang="en">
<head>
<meta charset="utf-8">
<title>TrimTable – Find &amp; Book Your Hairdresser</title>
<link rel="stylesheet" href="https://fonts.googleapis.com/css2?family=Lato:ital,wght@0,300;0,400;0,700;0,900;1,400;1,700&display=swap">
<style>
:root{
  --green:#abd036;
  --green-dark:#8fb423;
  --orange:#f37021;
  --grey-light:#c3c3c3;
  --grey:#757575;
  --ink:#333333;
  --paper:#ffffff;
  --mist:#f1f1f1;
  --footer:#3b3b3b;
  --footer-text:#bdbdbd;
}
*{box-sizing:border-box;margin:0;padding:0}
html,body{width:1200px;height:3020px;overflow:hidden}
body{font-family:"Lato",Arial,sans-serif;color:var(--ink);background:var(--paper);position:relative}
a{color:inherit;text-decoration:none}

/* Top bar */
.topbar{height:76px;display:flex;align-items:center;padding:0 60px;position:relative}
.brand{display:flex;align-items:center;gap:10px;font-weight:900;font-size:30px;color:var(--green)}
.brand-square{width:30px;height:30px;background:var(--green);border-radius:4px}
.book-btn{position:absolute;left:548px;top:22px;height:34px;padding:0 22px;background:var(--orange);color:#fff;font-size:15px;font-weight:700;display:flex;align-items:center;gap:8px;border-radius:2px}
.account{position:absolute;right:60px;top:18px;display:flex;gap:26px;font-size:12px;color:var(--grey)}
.account div{line-height:1.3}
.account b{color:var(--orange);font-weight:700;display:block}
.flag{width:28px;height:18px;display:flex;flex-direction:column;margin-top:6px}
.flag i{flex:1}

/* Nav */
.mainnav{height:34px;background:var(--green);display:flex;justify-content:space-around;padding:0 110px}
.mainnav a{color:#fff;font-size:13px;font-weight:700;letter-spacing:.5px;line-height:34px;padding:0 22px}
.mainnav a.active{background:var(--orange)}

/* Hero */
.hero{position:relative;height:510px}
.hero-photo{position:absolute;inset:0;background:linear-gradient(180deg,#e9e7e3 0%,#cfcac4 45%,#8d8985 100%)}
.hero-content{position:absolute;left:0;right:0;top:210px;text-align:center;color:#fff}
.hero-pin{width:44px;height:44px;margin:0 auto 10px}
.hero h1{font-size:38px;font-weight:400;line-height:1.2;text-shadow:0 2px 6px rgba(0,0,0,.35)}
.search{margin:34px auto 0;display:flex;justify-content:center;gap:0}
.search-field{width:400px;height:44px;background:#fff;color:var(--ink);font-size:16px;display:flex;align-items:center;padding:0 16px}
.search-btn{width:50px;height:44px;background:var(--green);display:flex;align-items:center;justify-content:center}

/* Stats */
.stats{height:410px;text-align:center;padding-top:52px}
.stats h2{font-size:30px;font-weight:400;color:var(--orange)}
.stats h2 em{font-style:italic;color:var(--ink)}
.stat-row{display:flex;justify-content:center;gap:84px;margin-top:46px}
.stat{width:110px}
.stat-pin{position:relative;width:110px;height:150px}
.stat-pin svg{position:absolute;inset:0}
.stat-pin span{position:absolute;top:42px;left:0;right:0;color:#fff;font-size:20px;font-weight:700}
.stat p{margin-top:14px;font-size:14px;color:var(--grey);line-height:1.3}

/* App band */
.app{height:320px;background:var(--green);position:relative}
.app-phones{position:absolute;left:130px;top:20px;width:440px;height:290px;background:linear-gradient(160deg,#f4f4f4,#d8d8d8);border-radius:10px}
.app-copy{position:absolute;left:700px;top:70px;width:380px;color:#fff}
.app-copy h2{font-size:30px;font-weight:400;line-height:1.2}
.app-copy p{margin-top:18px;font-size:15px;line-height:1.5}
.app-btn{display:inline-block;margin-top:18px;background:var(--orange);color:#fff;font-size:14px;font-weight:700;padding:10px 22px;border-radius:2px}

/* Steps */
.steps{height:480px;text-align:center;padding-top:60px;position:relative}
.steps h2{font-size:32px;font-weight:400;color:var(--orange)}
.steps h3{font-size:28px;font-weight:400;font-style:italic;color:var(--ink);margin-top:8px}
.steps-diagram{position:absolute;left:120px;top:170px;width:960px;height:200px}
.step-label{position:absolute;font-size:15px;color:var(--ink);line-height:1.3;width:180px;text-align:center}
.how-btn{position:absolute;left:50%;transform:translateX(-50%);top:390px;background:#1e1e1e;color:#fff;font-size:12px;font-weight:700;padding:11px 22px;letter-spacing:.5px}

/* Testimonials */
.clients{height:420px;background:var(--mist);text-align:center;padding-top:40px;position:relative}
.clients h2{font-size:32px;font-weight:400;color:var(--orange)}
.clients .sub{font-size:17px;font-style:italic;color:var(--grey);margin-top:6px}
.avatar{width:120px;height:120px;border-radius:50%;margin:34px auto 0;background:linear-gradient(180deg,#d7d7d7,#9c9c9c);border:4px solid #fff}
.client-name{margin-top:16px;font-size:20px;color:var(--green-dark);font-weight:700}
.client-quote{width:900px;margin:14px auto 0;font-size:13px;color:var(--grey);line-height:1.6;font-style:italic;position:relative}
.quote-mark{position:absolute;font-size:48px;color:var(--grey-light);font-style:normal;line-height:1}
.arrow{position:absolute;top:200px;color:var(--grey-light)}

/* Appointment form */
.booking{height:500px;position:relative}
.booking-bg{position:absolute;inset:0;background:linear-gradient(120deg,#efeeec 0%,#e2dfdb 60%,#d4d0cb 100%)}
.form-card{position:absolute;left:120px;top:50px;width:520px;height:400px;background:rgba(255,255,255,.75);padding:28px}
.row{display:flex;gap:16px;margin-bottom:16px}
.field{flex:1;height:40px;border:1px solid var(--grey-light);background:#fff;font-size:13px;color:var(--grey);display:flex;align-items:center;justify-content:space-between;padding:0 12px}
.field.area{height:84px;align-items:flex-start;padding-top:12px}
.cal{width:18px;height:18px;background:var(--orange);border-radius:2px}
.caret{width:0;height:0;border-left:5px solid transparent;border-right:5px solid transparent;border-top:6px solid var(--grey)}
.get-btn{display:inline-block;margin-top:4px;background:var(--green);color:#fff;font-size:13px;font-weight:700;padding:12px 26px;letter-spacing:.5px}
.booking-copy{position:absolute;left:730px;top:180px;width:380px}
.booking-copy h2{font-size:30px;font-weight:400;color:var(--orange)}
.booking-copy p{font-size:30px;font-style:italic;color:var(--ink);line-height:1.3;margin-top:10px}

/* Footer */
.footer{position:absolute;left:0;right:0;top:2740px;height:280px;background:var(--footer);color:var(--footer-text);display:flex;padding:44px 120px 0;gap:70px;font-size:13px}
.footer h4{color:#fff;font-size:16px;font-weight:700;margin-bottom:14px}
.footer ul{list-style:none}
.footer li{margin-bottom:9px}
.footer li::before{content:"› ";color:var(--green)}
.col-links{width:150px}
.col-contact{width:220px;line-height:1.5}
.col-hours{width:200px;line-height:1.5}
.col-hours b{color:#fff;font-weight:700;display:block}
.col-brand{margin-left:auto;text-align:right}
.col-brand .brand{color:#e0e0e0;font-size:26px;justify-content:flex-end}
.col-brand .brand-square{background:#e0e0e0;width:26px;height:26px}
.socials{display:flex;gap:6px;justify-content:flex-end;margin:22px 0 14px}
.socials i{width:24px;height:24px;background:#e0e0e0;border-radius:2px}
.contact-line{display:flex;gap:8px;margin-top:10px;align-items:center}
</style>
</head>
<body>

<header class="topbar">
  <a class="brand" href="#"><span class="brand-square"></span>TrimTable</a>
  <a class="book-btn" href="#">
    <svg width="16" height="16" viewBox="0 0 16 16"><rect x="1" y="3" width="14" height="12" fill="none" stroke="#fff" stroke-width="1.6"/><line x1="1" y1="7" x2="15" y2="7" stroke="#fff" stroke-width="1.6"/><line x1="5" y1="1" x2="5" y2="4" stroke="#fff" stroke-width="1.6"/><line x1="11" y1="1" x2="11" y2="4" stroke="#fff" stroke-width="1.6"/></svg>
    Book An Appointment</a>
  <div class="account">
    <div>New User?<b>Sign Up</b></div>
    <div>Already User?<b>Sign In</b></div>
    <div class="flag"><i style="background:#ae1c28"></i><i style="background:#fff;border:1px solid #eee"></i><i style="background:#21468b"></i></div>
  </div>
</header>

<nav class="mainnav">
  <a class="active" href="#">HOME</a>
  <a href="#">ABOUT US</a>
  <a href="#">HOW IT WORKS</a>
  <a href="#">TESTIMONIALS</a>
  <a href="#">CONTACT US</a>
</nav>

<section class="hero">
  <div class="hero-photo" role="img" aria-label="Bright modern hair salon interior with styling chairs and mirrors"></div>
  <div class="hero-content">
    <svg class="hero-pin" viewBox="0 0 44 44"><circle cx="22" cy="22" r="21" fill="rgba(0,0,0,.35)"/><path d="M22 10a8 8 0 0 0-8 8c0 6 8 15 8 15s8-9 8-15a8 8 0 0 0-8-8z" fill="#fff"/><circle cx="22" cy="18" r="3" fill="#777"/></svg>
    <h1>The Greatest Hairdresser Bookings Site In<br>The Netherlands With 542 Hairdressers.</h1>
    <div class="search">
      <div class="search-field">Salon Naam Post Code</div>
      <div class="search-btn"><svg width="20" height="20" viewBox="0 0 20 20"><circle cx="8" cy="8" r="6" fill="none" stroke="#fff" stroke-width="2.4"/><line x1="12.5" y1="12.5" x2="18" y2="18" stroke="#fff" stroke-width="2.6"/></svg></div>
    </div>
  </div>
</section>

<section class="stats">
  <h2>Last appointment on <em>October 16, 2015 at 13:54</em></h2>
  <div class="stat-row">
    <div class="stat"><div class="stat-pin"><svg viewBox="0 0 110 150"><path d="M55 2a53 53 0 0 0-53 53c0 38 53 93 53 93s53-55 53-93A53 53 0 0 0 55 2z" fill="#abd036"/></svg><span>125.22</span></div><p>Salons</p></div>
    <div class="stat"><div class="stat-pin"><svg viewBox="0 0 110 150"><path d="M55 2a53 53 0 0 0-53 53c0 38 53 93 53 93s53-55 53-93A53 53 0 0 0 55 2z" fill="#abd036"/></svg><span>323</span></div><p>Treatments For<br>Booking</p></div>
    <div class="stat"><div class="stat-pin"><svg viewBox="0 0 110 150"><path d="M55 2a53 53 0 0 0-53 53c0 38 53 93 53 93s53-55 53-93A53 53 0 0 0 55 2z" fill="#abd036"/></svg><span>340.78</span></div><p>Agreements</p></div>
    <div class="stat"><div class="stat-pin"><svg viewBox="0 0 110 150"><path d="M55 2a53 53 0 0 0-53 53c0 38 53 93 53 93s53-55 53-93A53 53 0 0 0 55 2z" fill="#abd036"/></svg><span>543.2</span></div><p>Hairdressers<br>Booking</p></div>
    <div class="stat"><div class="stat-pin"><svg viewBox="0 0 110 150"><path d="M55 2a53 53 0 0 0-53 53c0 38 53 93 53 93s53-55 53-93A53 53 0 0 0 55 2z" fill="#abd036"/></svg><span>986</span></div><p>Reliable Reviews</p></div>
  </div>
</section>

<section class="app">
  <div class="app-phones" role="img" aria-label="Two smartphones showing the TrimTable mobile app"></div>
  <div class="app-copy">
    <h2>All The Hairdressers Of<br>Netherlands <em>In Your Pocket !</em></h2>
    <p>Download The Droidix App And Always Find<br>A Place To Make A A Good Hairday Of.</p>
    <a class="app-btn" href="#">Download Droidix APP</a>
  </div>
</section>

<section class="steps">
  <h2>It's Very Easy 3 Step Process!</h2>
  <h3>Here's How It Works...</h3>
  <svg class="steps-diagram" viewBox="0 0 960 200">
    <path d="M20 110 Q 240 110 480 40" fill="none" stroke="#f37021" stroke-width="2"/>
    <path d="M480 40 Q 720 110 940 110" fill="none" stroke="#f37021" stroke-width="2"/>
    <circle cx="20" cy="110" r="5" fill="#f37021"/><circle cx="940" cy="110" r="5" fill="#f37021"/>
    <!-- search -->
    <circle cx="150" cy="110" r="34" fill="#fff" stroke="#f37021" stroke-width="3"/>
    <circle cx="139" cy="112" r="9" fill="none" stroke="#f37021" stroke-width="3"/>
    <circle cx="161" cy="112" r="9" fill="none" stroke="#f37021" stroke-width="3"/>
    <line x1="148" y1="110" x2="152" y2="110" stroke="#f37021" stroke-width="3"/>
    <!-- book online -->
    <circle cx="480" cy="40" r="34" fill="#abd036"/>
    <rect x="462" y="26" width="36" height="24" rx="2" fill="none" stroke="#fff" stroke-width="3"/>
    <line x1="472" y1="58" x2="488" y2="58" stroke="#fff" stroke-width="3"/>
    <line x1="480" y1="50" x2="480" y2="58" stroke="#fff" stroke-width="3"/>
    <!-- enjoy -->
    <circle cx="810" cy="110" r="34" fill="#fff" stroke="#f37021" stroke-width="3"/>
    <path d="M796 110 l9 9 l18 -18" fill="none" stroke="#f37021" stroke-width="4" stroke-linecap="round" stroke-linejoin="round"/>
  </svg>
  <div class="step-label" style="left:180px;top:330px">Search &amp; Find<br>Hairdresser</div>
  <div class="step-label" style="left:510px;top:262px">Book Your<br>Appointment Online</div>
  <div class="step-label" style="left:840px;top:330px">Enjoy Your<br>New Hairstyle</div>
  <a class="how-btn" href="#">SEE HOW IT WORKS</a>
</section>

<section class="clients">
  <h2>Happy Clients</h2>
  <p class="sub">Lorem ipsum dolor sit amet kowwek</p>
  <svg class="arrow" style="left:140px" width="14" height="24" viewBox="0 0 14 24"><path d="M12 2 L2 12 L12 22" fill="none" stroke="currentColor" stroke-width="2.5"/></svg>
  <svg class="arrow" style="right:140px" width="14" height="24" viewBox="0 0 14 24"><path d="M2 2 L12 12 L2 22" fill="none" stroke="currentColor" stroke-width="2.5"/></svg>
  <div class="avatar" role="img" aria-label="Portrait of a happy client"></div>
  <p class="client-name">Vestibulum porta, dual quis</p>
  <p class="client-quote"><span class="quote-mark" style="left:-40px;top:-8px">“</span>Lorem ipsum dolor sit amet, consectetur adipiscing elit. Integer venenatis tincidunt elit, aliquam semper quam pulvinar id.<br>Aliquam erat volutpat. Integer nulla urna, sagittis sed diam a, porta, tincidunt sed felis pharetra eleifend arcu at diam.<span class="quote-mark" style="right:-40px;top:14px">”</span></p>
</section>

<section class="booking">
  <div class="booking-bg" role="img" aria-label="Soft background of an appointment calendar and salon tools"></div>
  <form class="form-card">
    <div class="row"><div class="field">Name</div><div class="field">Email Address</div></div>
    <div class="row"><div class="field">Phone Number</div><div class="field">Appointment Type <span class="caret"></span></div></div>
    <div class="row"><div class="field">Appointment Date <span class="cal"></span></div><div class="field">Appointment Time <span class="caret"></span></div></div>
    <div class="row"><div class="field area">Comments</div></div>
    <a class="get-btn" href="#">GET APPOINTMENT</a>
  </form>
  <div class="booking-copy">
    <h2>What Are You Waiting For?</h2>
    <p>Make An Appointment At<br>The Hairdresser !</p>
  </div>
</section>

<footer class="footer">
  <div class="col-links">
    <h4>Quick Links</h4>
    <ul><li>Home</li><li>About Us</li><li>How It Works</li><li>Testimonials</li><li>Contact Us</li></ul>
  </div>
  <div class="col-contact">
    <h4>Contact Details</h4>
    <div class="contact-line"><svg width="14" height="18" viewBox="0 0 14 18"><path d="M7 1a6 6 0 0 0-6 6c0 4 6 10 6 10s6-6 6-10a6 6 0 0 0-6-6z" fill="#abd036"/></svg><span>TrimTable B.V.<br>Keizersgracht 120 Street<br>1015 CW Amsterdam</span></div>
    <div class="contact-line"><svg width="16" height="16" viewBox="0 0 16 16"><path d="M3 1h3l1 4-2 1c1 2 3 4 5 5l1-2 4 1v3c0 1-1 2-2 2C7 15 1 9 1 3c0-1 1-2 2-2z" fill="#abd036"/></svg><span>(123) 456 7890</span></div>
    <div class="contact-line"><svg width="16" height="12" viewBox="0 0 16 12"><rect x="1" y="1" width="14" height="10" fill="none" stroke="#abd036" stroke-width="1.6"/><path d="M1 1l7 6 7-6" fill="none" stroke="#abd036" stroke-width="1.6"/></svg><span>info@trimtable.com</span></div>
  </div>
  <div class="col-hours">
    <h4>Hours of Operations</h4>
    <b>Monday to Friday</b>09:00 am to 06:00 pm<br>
    <b style="margin-top:8px">Saturday</b>10:00 am to 04:00 pm<br>
    <b style="margin-top:8px">Sunday – Closed</b>
  </div>
  <div class="col-brand">
    <div class="brand"><span class="brand-square"></span>TrimTable</div>
    <div class="socials"><i></i><i></i><i></i><i></i></div>
    <p>Copyright 2015 TrimTable.<br>All Rights Reserved.</p>
  </div>
</footer>

</body>
</html>
```